Business Card Design for my Real Estate Investing Company

This is for a Real Estate Investing Company that will be serving the Las Vegas Valley. Id like the following slogan included: "Investing in Our Community" I have attached my logo. You will see the color tones I'm interested in..in my logo. I would like the card to be double-sided with a modern, professional look.
Target Market(s)
Homeowners, banks, real estate industry
Industry/Entity Type
Real Estate
Contact Information for Business Card
name: Dale Harwick
position: Managing Member
address: 4821 Corliss Pkwy ste 207-300
N. Las Vegas, NV 89084
phone: (702) 555-0143
fax: (702) 555-0187
email: SummitRidgeEstate@hollowmail.test
web: SummitRidgeEstates.test
*At the bottom of the card I would like....
We buy houses for cash....no repairs, no commissions, no fees!
Logo Text
SUMMIT RIDGE ESTATES "Investing in Our Community"
Font styles to use
Other font styles liked:
- Lora
Requirements
Must have
- On the back of the card, i'd like to have my logo large and the following statements:
- Are you considering selling your home? Want a simple, hassle-free transaction? We can help! We buy houses for cash and can close quickly! No need to do any repairs, no realtor commissions, no closing costs.....and no headaches. Let us help you with your real estate needs...!
Nice to have
- multiple colors 2 two tone on front and back

```html
<!DOCTYPE html>
<html lang="en">
<head>
<meta charset="utf-8">
<title>Summit Ridge Estates – Business Card</title>
<link rel="stylesheet" href="https://fonts.googleapis.com/css2?family=Lora:wght@500;600&family=Montserrat:wght@400;500&family=Oswald:wght@600&display=swap">
<style>
  :root {
    --bg: #3a3a3c;
    --card: #ffffff;
    --blue: #1f5db3;
    --grey: #8e8e8e;
    --ink: #1d1d1f;
  }
  * { box-sizing: border-box; margin: 0; padding: 0; }
  html, body { width: 1200px; height: 900px; overflow: hidden; }
  body { background: var(--bg); position: relative; font-family: "Montserrat", sans-serif; color: var(--ink); }

  .card {
    position: absolute;
    width: 640px; height: 366px;
    background: var(--card);
    border-radius: 22px;
    box-shadow: 0 14px 30px rgba(0,0,0,.45);
  }
  .card--back { left: 90px; top: 60px; }
  .card--front { left: 470px; top: 474px; }

  /* back side */
  .brand-mark {
    position: absolute; top: 58px; left: 0; right: 0;
    display: flex; justify-content: center; align-items: center; gap: 14px;
  }
  .brand-mark__square { width: 30px; height: 30px; background: var(--grey); }
  .brand-mark__name {
    font-family: "Lora", serif; font-weight: 600; font-size: 34px;
    color: var(--blue); letter-spacing: 1px;
  }
  .pitch {
    position: absolute; top: 150px; left: 40px; right: 40px;
    text-align: center; font-size: 15.5px; line-height: 1.42; font-weight: 500;
  }
  .tagline {
    position: absolute; bottom: 34px; left: 0; right: 0; text-align: center;
    font-family: "Oswald", sans-serif; font-weight: 600; font-size: 19px;
    color: var(--blue); letter-spacing: .3px;
  }

  /* front side */
  .logo-block { position: absolute; left: 38px; top: 118px; width: 250px; }
  .logo-block__row { display: flex; align-items: center; gap: 10px; }
  .logo-block__square { width: 22px; height: 22px; background: var(--grey); flex: none; }
  .logo-block__name {
    font-family: "Lora", serif; font-weight: 600; font-size: 22px; color: var(--blue);
    line-height: 1.05;
  }
  .logo-block__slogan {
    margin-top: 8px; font-family: "Lora", serif; font-weight: 500; font-size: 12px;
    letter-spacing: 1.5px; color: var(--ink); padding-left: 32px;
  }
  .contact { position: absolute; left: 330px; top: 90px; }
  .contact__name {
    font-family: "Lora", serif; font-weight: 500; font-size: 30px; color: var(--blue);
    letter-spacing: .5px; line-height: 1;
  }
  .contact__title { font-size: 15px; margin-top: 4px; }
  .contact__address { font-size: 15px; line-height: 1.35; margin-top: 16px; }
  .contact__list { list-style: none; margin-top: 14px; font-size: 15px; line-height: 1.45; }
  .contact__list li { display: flex; align-items: center; gap: 10px; }
  .contact__icon { width: 13px; height: 13px; flex: none; fill: none; stroke: var(--blue); stroke-width: 1.8; }
</style>
</head>
<body>

<section class="card card--back" aria-label="Card back">
  <div class="brand-mark">
    <span class="brand-mark__square"></span>
    <span class="brand-mark__name">SUMMIT RIDGE ESTATES</span>
  </div>
  <p class="pitch">
    Are you considering selling your home?<br>
    Want a simple, hassle-free transaction?<br>
    We can help! We buy houses for cash and can close quickly!<br>
    No need to do any repairs, no realtor commissions, no closing costs<br>
    and no headaches. Let us help you with your real estate needs...!
  </p>
  <p class="tagline">WE BUY HOUSES FOR CASH....NO REPAIRS, NO COMMISSIONS, NO FEES!</p>
</section>

<section class="card card--front" aria-label="Card front">
  <div class="logo-block">
    <div class="logo-block__row">
      <span class="logo-block__square"></span>
      <span class="logo-block__name">SUMMIT RIDGE ESTATES</span>
    </div>
    <p class="logo-block__slogan">"Investing in Our Community"</p>
  </div>

  <div class="contact">
    <h1 class="contact__name">DALE HARWICK</h1>
    <p class="contact__title">Managing Member</p>
    <p class="contact__address">4821 Corliss Pkwy ste 207-300<br>N. Las Vegas, NV 89084</p>
    <ul class="contact__list">
      <li>
        <svg class="contact__icon" viewBox="0 0 16 16"><path d="M3 2h3l1.5 3.5-2 1.2a8 8 0 0 0 3.8 3.8l1.2-2L14 10v3a1 1 0 0 1-1 1A11 11 0 0 1 2 3a1 1 0 0 1 1-1z"/></svg>
        (702) 555-0143
      </li>
      <li>
        <svg class="contact__icon" viewBox="0 0 16 16"><rect x="2" y="6" width="12" height="6" rx="1"/><path d="M4 6V2h8v4M4 12v2h8v-2"/></svg>
        (702) 555-0187
      </li>
      <li>
        <svg class="contact__icon" viewBox="0 0 16 16"><rect x="1.5" y="3.5" width="13" height="9" rx="1"/><path d="M1.5 4l6.5 5 6.5-5"/></svg>
        SummitRidgeEstate@hollowmail.test
      </li>
      <li>
        <svg class="contact__icon" viewBox="0 0 16 16"><circle cx="8" cy="8" r="6.3"/><path d="M1.7 8h12.6M8 1.7c-3 3.5-3 9.1 0 12.6M8 1.7c3 3.5 3 9.1 0 12.6"/></svg>
        www.SummitRidgeEstates.test
      </li>
    </ul>
  </div>
</section>

</body>
</html>
```